Build a landing page to promote a service (dialler consultation and support).

We are a call centre consultation firm and we need a landing page to promote a service. The service is Tormalux dialler consultation and support.
If you do not know what Tormalux is, please do some quick "Zorvex" research for more information.
The landing page will be promoted with a paid advertisement, so we want something that is simple, and explains exactly what service we offer.
There are two objectives for the landing page:
1) A "call to action" which directs the user to a contact page, including a form plus all of our contact details.
2) A form for them viewers to enter their details to get a "FREE" quote for their project. This form should be placed on the main page.
Notes:
The call to action will require the viewer to enter their name, email, phone number as well as a description of their request. There will also need to be a drop down menu for the type of quote. This menu should have the following options:
1) Tormalux support
2) Tormalux hosting
3) Tormalux customisation
4) Other
We need 2 pages in total:
1) Main landing page
This is the home page. It will need to clearly indicate our services and our key selling features.
Services:
* Tormalux support
* Tormalux hosting
* Tormalux customisation
Key Selling Features:
* Australian based
* PCI complaint
* 10+ years of dialler and call centre experience
* we run a sister company which is a highly reputable 40 seat call centre, so we know first hand about call centre technology.
The main landing page will have an "about us" section with a few paragraphs about how we got started.
-------------------------------------------------------------------------
2) Contact page
All of our contact details will live on this page, as well as a contact form.
Other notes:
We will be self hosting the landing page.
We already have a domain name.
The design must be clean and incorporate our logo, as well as it's colours. (Logo attached)
We want a fully function HTML landing page, not just a "PSD" design.
The page must be mobile optimised.
Anyone using Tormalux software.

```html
<!DOCTYPE html>
<html lang="en">
<head>
<meta charset="utf-8">
<title>NexaCall – Tormalux Consultation and Support</title>
<link href="https://fonts.googleapis.com/css2?family=Montserrat:wght@400;500;600&family=Varela+Round&display=swap" rel="stylesheet">
<style>
:root{
  --teal:#22ab92;
  --blue:#1a7ac6;
  --ink:#1e1e1e;
  --muted:#333;
  --field:#eeeeee;
  --white:#ffffff;
}
*{margin:0;padding:0;box-sizing:border-box}
html,body{width:1200px;height:2927px;overflow:hidden;background:var(--white)}
body{position:relative;font-family:'Montserrat',sans-serif;color:var(--ink)}
.abs{position:absolute}
.heading{font-family:'Varela Round',sans-serif;font-weight:400}
.btn{position:absolute;display:flex;align-items:center;justify-content:center;background:var(--teal);color:var(--white);font-family:'Montserrat',sans-serif;font-weight:600;font-size:15px;text-transform:uppercase;letter-spacing:.3px}

/* hero */
.hero-photo{position:absolute;left:0;top:0;width:1200px;height:640px;background:linear-gradient(90deg,#f3f6f8 0%,#e9eef2 35%,#c9d3da 55%,#9aa7b0 80%,#6f7d88 100%)}
.hero-edge{position:absolute;left:0;top:600px}
.logo{position:absolute;left:100px;top:10px;width:130px;height:72px}
.logo-mark{position:absolute;left:40px;top:0;width:40px;height:40px;border-radius:50%;background:var(--blue)}
.logo-name{position:absolute;left:0;top:46px;width:130px;text-align:center;font-family:'Varela Round',sans-serif;font-size:22px;color:var(--blue)}
.nav{position:absolute;top:30px;font-size:16.5px;color:#222}
.nav-active{position:absolute;left:474px;top:0;width:63px;height:5px;background:var(--teal)}
.contact-btn{left:954px;top:25px;width:146px;height:39px;font-size:15px}
.hero-title{position:absolute;left:100px;top:170px;font-size:58px;color:var(--blue)}
.features{position:absolute;left:100px;top:276px;list-style:none}
.features li{display:flex;align-items:center;height:41px;margin-bottom:19.5px;font-size:19px;font-weight:500;color:#1d1d1d}
.features .num{width:41px;height:41px;border-radius:50%;background:var(--teal);color:var(--white);font-size:15px;display:flex;align-items:center;justify-content:center;margin-right:31px}
.dot{position:absolute;top:571px;width:15px;height:15px;border-radius:50%;border:2px solid #9aa0a6}
.dot.on{background:var(--blue);border-color:var(--blue)}

/* services */
.section-title{position:absolute;font-size:40px;color:var(--ink)}
.services-text{position:absolute;left:101px;top:813px;width:710px;font-size:14.5px;line-height:35px;color:var(--muted)}
.service{position:absolute;top:953px;width:214px;height:214px;border-radius:50%;border:3px solid var(--teal);display:flex;align-items:center;justify-content:center}
.service-inner{width:196px;height:196px;border-radius:50%;background:var(--blue);color:var(--white);display:flex;flex-direction:column;align-items:center;justify-content:center;text-align:center;font-size:19px;font-weight:500;line-height:25px}
.service-inner svg{margin-bottom:12px}

/* company */
.company-photo{position:absolute;left:0;top:1290px}
.company-band{position:absolute;left:0;top:1331px}
.company-title{position:absolute;left:597px;top:1378px;font-size:39px;color:var(--white)}
.company-text{position:absolute;left:599px;top:1440px;width:510px;font-size:14px;line-height:34px;color:var(--white)}
.outline-btn{position:absolute;left:599px;top:1572px;width:172px;height:45px;border:2px solid var(--white);color:var(--white);display:flex;align-items:center;justify-content:center;font-size:15px;font-weight:600}

/* quote */
.quote-title{left:0;width:1200px;text-align:center;top:1835px;font-size:41px}
.quote-sub{position:absolute;left:0;width:1200px;text-align:center;top:1896px;font-size:15px;color:#222}
.field{position:absolute;background:var(--field);border:1px solid #e2e2e2;font-size:11.5px;color:#555;text-transform:uppercase;padding:0 17px;display:flex;align-items:center}
.field.area{align-items:flex-start;padding-top:20px}
.select-caret{position:absolute;right:20px;top:24px;width:0;height:0;border-left:6px solid transparent;border-right:6px solid transparent;border-top:6px solid #555}
.agent-photo{position:absolute;left:868px;top:1922px;width:254px;height:429px;border-radius:120px 120px 0 0;background:linear-gradient(180deg,#e9ded6 0%,#f4f4f4 45%,#dfe1e4 85%,#3a3a3a 100%)}

/* story */
.story{position:absolute;left:0;top:2351px;width:1200px;height:431px;background:var(--blue)}
.story-title{left:0;width:1200px;text-align:center;top:2448px;font-size:41px;color:var(--white)}
.story-text{position:absolute;left:137px;width:926px;top:2505px;text-align:center;font-size:15px;line-height:33px;color:var(--white)}
.story-edge{position:absolute;left:0;top:2751px}

/* footer */
.social{position:absolute;top:2829px;width:46px;height:46px;border-radius:50%;border:2px solid var(--teal)}
.copyright{position:absolute;left:0;width:1200px;text-align:center;top:2897px;font-size:12px;color:#333}
</style>
</head>
<body>

<header>
  <div class="hero-photo" role="img" aria-label="Photo of smiling call centre agents wearing headsets at their desks"></div>
  <svg class="hero-edge" width="1200" height="40" viewBox="0 0 1200 40" aria-hidden="true">
    <polygon points="0,0 0,40 1200,40 1200,0 1083,7 1102,40 117,40 98,7" fill="none"/>
    <polygon points="0,0 1200,0 1200,40 0,40" fill="transparent"/>
    <polygon points="98,7 1083,7 1102,40 117,40" fill="#ffffff"/>
    <rect x="0" y="40" width="1200" height="0" fill="#fff"/>
  </svg>

  <div class="logo">
    <div class="logo-mark"></div>
    <div class="logo-name">NexaCall</div>
  </div>

  <nav>
    <div class="nav-active"></div>
    <span class="nav" style="left:484px">Home</span>
    <span class="nav" style="left:562px">Company</span>
    <span class="nav" style="left:667px">Services</span>
    <span class="nav" style="left:761px">Info</span>
    <span class="nav" style="left:821px">Advantages</span>
  </nav>
  <a class="btn contact-btn">Contact Now</a>

  <h1 class="hero-title heading">NexaCall</h1>
  <ul class="features">
    <li><span class="num">01.</span>Australian based</li>
    <li><span class="num">02.</span>PCI complaint</li>
    <li><span class="num">03.</span>10+ years experience</li>
    <li><span class="num">04.</span>40 seat call centre</li>
  </ul>
  <span class="dot on" style="left:100px"></span>
  <span class="dot" style="left:128px"></span>
  <span class="dot" style="left:153px"></span>
  <span class="dot" style="left:180px"></span>
</header>

<section class="services">
  <h2 class="section-title heading" style="left:98px;top:749px">Our Services</h2>
  <p class="services-text">Sed ut perspiciatis unde omnis iste natus error sit voluptatem accusantium remque litium, totam rem aperiam, eaque ipsa quae ab illo inventore veritatis et quasi architecto beatae vitae dicta sunt explicabo.</p>
  <a class="btn" style="left:813px;top:827px;width:184px;height:45px">Get Started</a>

  <div class="service" style="left:90px">
    <div class="service-inner">
      <svg width="48" height="44" viewBox="0 0 48 44" fill="none" stroke="#fff" stroke-width="3"><path d="M6 28V22a18 18 0 0 1 36 0v6"/><rect x="4" y="24" width="8" height="14" rx="3"/><rect x="36" y="24" width="8" height="14" rx="3"/><path d="M40 38c0 4-6 5-12 5"/></svg>
      Tormalux support
    </div>
  </div>
  <div class="service" style="left:359px">
    <div class="service-inner">
      <svg width="50" height="48" viewBox="0 0 50 48" fill="none" stroke="#fff" stroke-width="2.5"><circle cx="25" cy="13" r="11"/><path d="M14 13h22M25 2c-6 6-6 16 0 22M25 2c6 6 6 16 0 22M25 24v8M6 32h38M6 32v6M25 32v6M44 32v6"/><rect x="2" y="38" width="8" height="7"/><rect x="21" y="38" width="8" height="7"/><rect x="40" y="38" width="8" height="7"/></svg>
      Tormalux hosting
    </div>
  </div>
  <div class="service" style="left:627px">
    <div class="service-inner">
      <svg width="50" height="50" viewBox="0 0 50 50" fill="none" stroke="#fff" stroke-width="2.5"><circle cx="28" cy="22" r="14" stroke-dasharray="6 3"/><circle cx="28" cy="22" r="6"/><path d="M6 46l14-14"/></svg>
      Tormalux<br>customisation
    </div>
  </div>
  <div class="service" style="left:896px">
    <div class="service-inner">
      <svg width="50" height="12" viewBox="0 0 50 12" fill="#fff"><circle cx="7" cy="6" r="4"/><circle cx="25" cy="6" r="4"/><circle cx="43" cy="6" r="4"/></svg>
      Other
    </div>
  </div>
</section>

<section class="company">
  <svg class="company-band" width="1200" height="343" viewBox="0 0 1200 343" aria-hidden="true"><polygon points="560,0 1200,0 1200,343 433,343" fill="#22ab92"/></svg>
  <svg class="company-photo" width="570" height="423" viewBox="0 0 570 423" role="img" aria-label="Photo of a smiling male call centre agent with a headset">
    <defs><linearGradient id="agentTone" x1="0" y1="0" x2="1" y2="0"><stop offset="0" stop-color="#3f6f96"/><stop offset=".5" stop-color="#7c8fa0"/><stop offset="1" stop-color="#c9b4a2"/></linearGradient></defs>
    <polygon points="0,0 570,0 425,423 0,423" fill="url(#agentTone)"/>
  </svg>
  <h2 class="company-title heading">Our Company</h2>
  <p class="company-text">Sed ut perspiciatis unde omnis iste natus error sit voluptatem accusantium doloremque laudantium, totam rem aperiam, eaque ipsa quae abveritatis et quasi architecto beatae vitae dicta sunt explicabo.</p>
  <a class="outline-btn">READ MORE</a>
</section>

<section class="quote">
  <h2 class="section-title heading quote-title">Get a "FREE" Quote</h2>
  <p class="quote-sub">Lorem ipsum dolor sit amet, consectetur adipiscing elit, sed do eiusmod tempor</p>
  <div class="field" style="left:100px;top:1949px;width:341px;height:53px">Name</div>
  <div class="field" style="left:457px;top:1949px;width:343px;height:53px">Email</div>
  <div class="field" style="left:100px;top:2017px;width:341px;height:53px">Phone No</div>
  <div class="field" style="left:457px;top:2017px;width:343px;height:53px">Select Service<span class="select-caret"></span></div>
  <div class="field area" style="left:100px;top:2086px;width:700px;height:97px">Description</div>
  <a class="btn" style="left:100px;top:2199px;width:202px;height:47px">Get a Free Quote</a>
  <div class="agent-photo" role="img" aria-label="Photo of a smiling female support agent with a headset, arms crossed"></div>
</section>

<section>
  <div class="story"></div>
  <h2 class="section-title heading story-title">How We Got Started</h2>
  <p class="story-text">"Lorem ipsum dolor sit amet, consectetur adipiscing elit, sed do eiusmod tempor incididunt ut labore et dolore magna aliqua. Ut enim ad minim veniam, quis nostrud exercitation ullamco laboris nisi ut aliquip ex ea commodo consequat. Duis aute irure dolor in repredenit in voluptate velit esse cillum dolore eu fugiat nulla pariatur.</p>
  <a class="btn" style="left:511px;top:2628px;width:178px;height:49px">Learn More</a>
  <svg class="story-edge" width="1200" height="31" viewBox="0 0 1200 31" aria-hidden="true"><polygon points="134,0 1102,0 1083,31 117,31" fill="#ffffff"/><polygon points="117,31 134,0 117,0 117,31" fill="none"/></svg>
</section>

<footer>
  <span class="social" style="left:445px" aria-label="Social link 1"></span>
  <span class="social" style="left:512px" aria-label="Social link 2"></span>
  <span class="social" style="left:578px" aria-label="Social link 3"></span>
  <span class="social" style="left:644px" aria-label="Social link 4"></span>
  <span class="social" style="left:711px" aria-label="Zorvex social link"></span>
  <p class="copyright">© Copyright NexaCall 2018 &nbsp;| &nbsp;All Rights Reserved &nbsp;| &nbsp;Privacy Policy &nbsp;| &nbsp;Terms Of Use &nbsp;| &nbsp;Faq</p>
</footer>

</body>
</html>
```